wealth management firm, professional group, new model

we have a logo that works but we need a card, white background using our colors...clean look

our tag line if can be used in

Steady Guidance For Lasting Growth

```html
<!DOCTYPE html>
<html lang="en">
<head>
<meta charset="utf-8">
<title>Arcon Wealth Partners — Business Card</title>
<link href="https://fonts.googleapis.com/css2?family=Montserrat:wght@400;500;700;800&display=swap" rel="stylesheet">
<style>
  :root {
    --navy: #10264a;
    --paper: #f4f0e8;
    --backdrop: #e6e1d7;
  }
  * { box-sizing: border-box; margin: 0; padding: 0; }
  html, body {
    width: 1200px;
    height: 896px;
    overflow: hidden;
    background: var(--backdrop);
    font-family: "Montserrat", sans-serif;
    color: var(--navy);
  }
  .sheet {
    width: 1200px;
    height: 896px;
    display: flex;
    align-items: center;
    justify-content: center;
    gap: 48px;
  }
  .card {
    width: 532px;
    height: 304px;
    background: var(--paper);
    box-shadow: 0 2px 6px rgba(0,0,0,0.08);
    display: flex;
    flex-direction: column;
    align-items: center;
    text-align: center;
  }
  /* Front */
  .card--front { justify-content: center; padding: 24px; }
  .wordmark {
    font-weight: 400;
    font-size: 66px;
    letter-spacing: 0.32em;
    margin-right: -0.32em;
    line-height: 1;
  }
  .wordmark-sub {
    font-weight: 400;
    font-size: 23px;
    letter-spacing: 0.14em;
    margin-right: -0.14em;
    margin-top: 10px;
  }
  .divider {
    width: 112px;
    height: 3px;
    background: var(--navy);
    margin: 18px 0 14px;
  }
  .tagline {
    font-weight: 800;
    font-size: 17px;
    letter-spacing: 0.01em;
    text-transform: uppercase;
  }
  /* Back */
  .card--back { padding: 34px 24px 28px; }
  .person-name {
    font-weight: 800;
    font-size: 30px;
    letter-spacing: 0.14em;
    margin-right: -0.14em;
    text-transform: uppercase;
    line-height: 1;
  }
  .person-title {
    font-weight: 400;
    font-size: 17px;
    margin-top: 6px;
  }
  .back-mark {
    font-weight: 400;
    font-size: 28px;
    letter-spacing: 0.32em;
    margin-right: -0.32em;
    margin: 34px 0 auto;
  }
  .contact {
    font-weight: 500;
    font-size: 16px;
    line-height: 1.4;
  }
</style>
</head>
<body>
  <main class="sheet">
    <section class="card card--front" aria-label="Card front">
      <div class="wordmark">ARCON</div>
      <div class="wordmark-sub">WEALTH PARTNERS</div>
      <div class="divider"></div>
      <p class="tagline">Steady Guidance For Lasting Growth</p>
    </section>

    <section class="card card--back" aria-label="Card back">
      <h1 class="person-name">Jordan Hale</h1>
      <p class="person-title">Senior Wealth Advisor</p>
      <div class="back-mark">ARCON</div>
      <p class="contact">
        jordan@arconwealth.com &nbsp;|&nbsp; +1 (555) 010-4821<br>
        arconwealth.com
      </p>
    </section>
  </main>
</body>
</html>
```